Business Card: RW Office Partners - Your organised problem solver

Business Name: RW Office Partners
Website: www.rwofficepartners.com.au
Email: marisol@rwofficepartners.com.au
Mobile: 61 482 907 236
Facebook: @rwofficepartners
Instrgram: @rwofficepartners

Brading Colours:
HEX
#986474
#ddccd3
#7a8498
#c9d8e4
#000000
#ffffff

Tag Line: Your organised problem solver

Link to DRAFT website:
https://deskhelpcollective.wixsite.com/rw-office-partners

About Page from the website:
My name is Marisol Wrenfield, and I would love to assist you to become more productive in your day to day and achieve your business and personal goals.
My mission is to give you time, time to work on the important tasks of your business or to be able to spend more time with your family. I will take on the tasks you don’t have time for, don’t know well or simply don’t like to do.
I have an extensive background in Administration, Tender Coordination, Document Control, WHS and Quality Management working primarily in the Construction, Mining and Corporate World.
I am passionate about being organised, having order and making things in your life (and mine) easier! I love to watch something unfold and grow into something amazing! I am known for being the go-to problem solver, the organiser of all things, producing high standards of work even under pressure. I’m also a confident communicator, and I understand that you’re busy running your business.

Target Market(s)

Small to Medium Business who require assistance in their business by a virtual assistant.

Industry/Entity Type

Virtual Assistant

Contact Information for Business Card

Mobile: 61 482 907 236

Font styles to use
Sans Serif

Colors
ffffff

Requirements
Must have
• Branding Colours as outlined.
Contact Details as outlined.
Logo as provided.
Proper contact details - mobile, facebook, instragm, website.
Simple, Elegant, very clean looking.
Should not have
• Note cute with pictures.
Not too girly as still want to market to construction companies.

```html
<!DOCTYPE html>
<html lang="en">
<head>
<meta charset="utf-8">
<title>RW Office Partners – Business Card</title>
<link href="https://fonts.googleapis.com/css2?family=Montserrat:wght@500;600;700&family=Roboto:wght@400;500&display=swap" rel="stylesheet">
<style>
  :root {
    --backdrop: #3b3b3d;
    --card: #1c1b1f;
    --mauve: #986474;
    --blush: #ddccd3;
    --slate: #7a8498;
    --mist: #c9d8e4;
    --silver: #8d8c92;
    --white: #ffffff;
  }
  * { margin: 0; padding: 0; box-sizing: border-box; }
  html, body { width: 799px; height: 1200px; overflow: hidden; }
  body {
    background: var(--backdrop);
    font-family: "Roboto", Arial, sans-serif;
    position: relative;
  }
  .card {
    position: absolute;
    left: 80px;
    width: 640px;
    height: 391px;
    background: var(--card);
    border-radius: 4px;
  }
  .card--front { top: 150px; }
  .card--back { top: 660px; }

  /* front */
  .brand-name {
    position: absolute;
    font-family: "Montserrat", Arial, sans-serif;
    font-weight: 600;
    letter-spacing: 0.02em;
  }
  .card--front .brand-name {
    left: 0; right: 0; top: 120px;
    text-align: center;
    font-size: 46px;
    color: var(--silver);
  }
  .socials {
    position: absolute;
    display: flex;
    align-items: center;
    gap: 22px;
    color: var(--white);
    font-size: 19px;
  }
  .card--front .socials { left: 60px; top: 290px; }
  .social { display: flex; align-items: center; gap: 8px; }
  .social-mark {
    width: 14px; height: 14px;
    background: var(--mauve);
    border-radius: 2px;
  }

  /* back */
  .card--back .brand-name {
    left: 46px; top: 92px;
    width: 230px;
    font-size: 44px;
    line-height: 1.1;
    color: var(--mauve);
  }
  .person {
    position: absolute;
    left: 330px; top: 110px;
  }
  .person-name {
    font-family: "Montserrat", Arial, sans-serif;
    font-weight: 700;
    font-size: 22px;
    color: var(--mauve);
  }
  .person-role {
    font-size: 16px;
    color: var(--white);
    margin-top: 4px;
  }
  .contact-list {
    list-style: none;
    margin-top: 16px;
    color: var(--white);
    font-size: 16px;
  }
  .contact-list li {
    display: flex;
    align-items: center;
    gap: 10px;
    height: 24px;
  }
  .contact-list svg { width: 14px; height: 14px; flex: none; }
  .card--back .socials {
    left: 0; right: 0; top: 318px;
    justify-content: center;
    gap: 18px;
    font-size: 17px;
  }
  .rule {
    width: 70px; height: 1px;
    background: var(--slate);
  }
</style>
</head>
<body>

<section class="card card--front" aria-label="Card front">
  <div class="brand-name">RW Office Partners</div>
  <div class="socials">
    <span class="social"><span class="social-mark"></span>@rwofficepartners</span>
    <span class="social"><span class="social-mark"></span>@rwofficepartners</span>
  </div>
</section>

<section class="card card--back" aria-label="Card back">
  <div class="brand-name">RW Office Partners</div>
  <div class="person">
    <div class="person-name">Marisol Wrenfield</div>
    <div class="person-role">Virtual Assistant</div>
    <ul class="contact-list">
      <li>
        <svg viewBox="0 0 14 14"><path d="M3 1h3l1 3-2 1a7 7 0 0 0 4 4l1-2 3 1v3a1 1 0 0 1-1 1A11 11 0 0 1 2 2a1 1 0 0 1 1-1z" fill="#986474"/></svg>
        61 482 907 236
      </li>
      <li>
        <svg viewBox="0 0 14 14"><rect x="1" y="3" width="12" height="8" fill="#986474"/><path d="M1 3l6 5 6-5" stroke="#1c1b1f" stroke-width="1.2" fill="none"/></svg>
        marisol@rwofficepartners.com.au
      </li>
      <li>
        <svg viewBox="0 0 14 14"><circle cx="7" cy="7" r="6" fill="none" stroke="#986474" stroke-width="1.4"/><path d="M1 7h12M7 1c-3 3-3 9 0 12M7 1c3 3 3 9 0 12" stroke="#986474" stroke-width="1" fill="none"/></svg>
        www.rwofficepartners.com.au
      </li>
    </ul>
  </div>
  <div class="socials">
    <span class="rule"></span>
    <span class="social"><span class="social-mark"></span>@rwofficepartners</span>
    <span class="social"><span class="social-mark"></span>@rwofficepartners</span>
    <span class="rule"></span>
  </div>
</section>

</body>
</html>
```